Dental Practice Billboard Design

We are a newer dental practice in need of a simple but appealing billboard for our growing dental practice to attract new patients. The practice is owned by husband and wife dentists and is family friendly in a small town in Kentucky. We try to be very friendly and caring to our patients. Would prefer a blue background for the billboard and our tooth logo to be prominent. We are partial to the Patua One font used in the image below but please feel free to tweak it as you deem necessary. The shape of the uppercase D and lowercase g are why we like that font, so fonts with a similarly shaped “D” and “g” would work as well. Please include our phone number (555) 847-1390. Please see our website Harlowbrookdentistry.example for more info on the practice if needed. Thank you! Looking forward to seeing your creation.
Updates

The dimensions will be 12ft x 24ft (3.6576m x 7.3152m). Apologies for not including this in the original prompt. Thank you all for your submissions.

Industry/Entity Type

Dental

Font styles to use
Other font styles liked:
• Patua One

Colors
0054AA
0677BA
7BADD7
CADEEF
E8F1F8
0094D4
00A9DD
6FCCEA
C7EBF8
E9F6FB
00AB8E
00BBA5
67D7C9
C6EFE9
E9F9F6
59FF00
82FF00
B8FF75
E3FFCB
F4FFEA

Requirements
Must have
• Phone number, website, Logo, Practice name “Harlow Brook Dentistry”
Should not have
• A tagline or slogan

```html
<!DOCTYPE html>
<html lang="en">
<head>
<meta charset="UTF-8">
<title>Harlow Brook Dentistry Billboard</title>
<link href="https://fonts.googleapis.com/css2?family=Patua+One&family=Montserrat:wght@800&display=swap" rel="stylesheet">
<style>
  :root {
    --page-bg: #e9f6fb;
    --navy: #1e1f6e;
    --green: #16b216;
    --white: #ffffff;
    --photo-top: #c9d6e6;
    --photo-bottom: #b9a88c;
  }
  * { margin: 0; padding: 0; box-sizing: border-box; }
  html, body {
    width: 1200px;
    height: 857px;
    overflow: hidden;
    background: var(--page-bg);
  }
  .billboard {
    position: absolute;
    left: 20px;
    top: 138px;
    width: 1160px;
    height: 580px;
    background: var(--navy);
    overflow: hidden;
  }
  .wave {
    position: absolute;
    inset: 0;
    width: 100%;
    height: 100%;
  }
  .brand {
    position: absolute;
    left: 70px;
    top: 56px;
    display: flex;
    align-items: center;
    gap: 26px;
  }
  .brand-dot {
    width: 96px;
    height: 96px;
    border-radius: 50%;
    background: var(--green);
    flex: none;
  }
  .brand-name {
    font-family: "Patua One", serif;
    color: var(--white);
    line-height: 1;
  }
  .brand-name .name-main { display: block; font-size: 88px; }
  .brand-name .name-sub { display: block; font-size: 56px; margin-top: 4px; }
  .website {
    position: absolute;
    left: 72px;
    top: 262px;
    font-family: "Patua One", serif;
    font-size: 42px;
    line-height: 1;
    color: var(--white);
  }
  .phone {
    position: absolute;
    left: 42px;
    top: 462px;
    display: flex;
    align-items: center;
    gap: 20px;
    font-family: "Montserrat", sans-serif;
    font-weight: 800;
    font-size: 66px;
    line-height: 1;
    color: var(--white);
    text-shadow: 2px 3px 4px rgba(0, 0, 0, 0.25);
  }
  .phone-icon { width: 64px; height: 64px; flex: none; }
  .family-photo {
    position: absolute;
    left: 770px;
    top: 190px;
    width: 390px;
    height: 390px;
    background: linear-gradient(180deg, var(--photo-top) 0%, #aebfd6 45%, var(--photo-bottom) 100%);
    border-radius: 190px 190px 0 0;
  }
</style>
</head>
<body>
  <section class="billboard">
    <svg class="wave" viewBox="0 0 1160 580" preserveAspectRatio="none" aria-hidden="true">
      <path d="M0 368 C 300 420, 600 470, 770 468 C 910 466, 1040 436, 1160 408 L1160 580 L0 580 Z" fill="#ffffff"/>
      <path d="M0 380 C 300 436, 600 488, 770 486 C 910 484, 1040 456, 1160 428 L1160 580 L0 580 Z" fill="#16b216"/>
    </svg>

    <div class="brand">
      <span class="brand-dot"></span>
      <h1 class="brand-name"><span class="name-main">Harlow Brook</span><span class="name-sub">Dentistry</span></h1>
    </div>

    <p class="website">Harlowbrookdentistry.example</p>

    <div class="phone">
      <svg class="phone-icon" viewBox="0 0 64 64" aria-hidden="true">
        <circle cx="32" cy="32" r="30" fill="#ffffff"/>
        <path d="M22 16 l7 -1 l4 10 l-5 4 c2 5 6 9 11 11 l4 -5 l10 4 l-1 7 c-1 3 -4 4 -7 4 C 30 48 16 34 16 23 c0 -3 2 -6 6 -7 Z" fill="#16b216"/>
      </svg>
      <span class="phone-number">(555) 847-1390</span>
    </div>

    <div class="family-photo" role="img" aria-label="Photo of a smiling family: father, mother and young daughter sitting together"></div>
  </section>
</body>
</html>
```